Modernize Website: marcusfellwright.net

I am a novelist with an older-generation website at: marcusfellwright.net.

I am hoping to refresh this outdated website with a new, responsive redesign. I would prefer to host the code myself, and edit using Adobe Dreamweaver. So I’m not looking to use a hosted site builder like Plexo. Nor am I looking to use a CMS like Pagecraft.

In order to simplify the old site, there are a number of sections I’ll be looking to remove during this redesign. These are shown in the "MF Site Redesign" attachment. I can also provide imagery for new content (another book series in addition to the existing one), as well as higher-resolution imagery (if needed) of the old content.

Happy to answer any further questions.
Updates

I've uploaded a ZIP file containing high-res artwork associated with the new trilogy of books.

Target Market(s)

Readers of epic fantasy novels such as H.W.B. Castellane's THE WARDEN OF THE VALES, Harold P.Q. Ventris's A CROWN OF ASH AND RAIN, Victor Halloway's THE GATE OF STARS, or Dennis Vale's BLADE OF MERIVANE.

Industry/Entity Type

Entertainment

Coding

Coded - Design and coding required

Number of Pages Required

5+ page

Font styles to use
Serif
Decorative

Colors

Designer to choose colors to be used in the design.

Requirements
Must have
• I'm looking for a responsive design that displays nicely on both mobile and desktop devices. Existing site contains multiple pages, but these can obviously be combined into fewer pages (or even one) by divisions such as tabs, sections, and/or modal windows. See marcusfellwright.net for current content and "MF Site Redesign" attachment for content to be removed at this time.
Nice to have
• The ability to fulfill orders of autographed books directly from the website. I currently use Coinlo to do this, but it would be nice to incorporate a more comprehensive merchant service at a reasonable rate.
Should not have
• I'd like to host and control the site code myself. So please don't use a hosted web builder like Plexo, or a cloud-based CMS like Pagecraft.

```html
<!DOCTYPE html>
<html lang="en">
<head>
<meta charset="utf-8">
<title>Marcus Fellwright — The Legend of Varethon</title>
<link href="https://fonts.googleapis.com/css2?family=Lato:wght@400;700;900&display=swap" rel="stylesheet">
<style>
:root{
  --ink:#222222;
  --black:#050505;
  --white:#ffffff;
  --red:#d4001a;
  --red-deep:#3f1a1e;
  --grey-bg:#f2f2f2;
  --btn-grey:#8c8c8c;
  --orange:#f7941d;
  --text:#333333;
  --hero-a:#0f2236;
  --hero-b:#2c4e6e;
}
*{margin:0;padding:0;box-sizing:border-box}
html,body{width:1200px;height:2628px;overflow:hidden}
body{position:relative;font-family:'Lato',sans-serif;color:var(--text);background:var(--white)}
.abs{position:absolute}

/* header */
.site-header{left:0;top:0;width:1200px;height:86px;background:var(--black)}
.brand-art{left:79px;top:4px;width:481px;height:78px;background:linear-gradient(90deg,rgba(40,50,70,.6),rgba(90,30,30,.5) 70%,rgba(0,0,0,0))}
.brand-name{left:79px;top:12px;font-size:30px;font-weight:400;color:var(--white);letter-spacing:1px;line-height:1}
.brand-tagline{left:355px;top:60px;font-size:14px;font-weight:700;color:var(--red);line-height:1}
.main-nav{right:75px;top:0;height:86px;display:flex;align-items:center;gap:58px}
.main-nav a{color:var(--white);text-decoration:none;font-size:14px;font-weight:700;letter-spacing:.5px}

/* hero */
.hero{left:0;top:86px;width:1200px;height:546px;background:radial-gradient(ellipse at 60% 40%,var(--hero-b),var(--hero-a) 75%)}
.hero-book{left:158px;top:19px;width:268px;height:527px;background:linear-gradient(160deg,#2a3a48,#5a2a1a 55%,#c0471a 85%,#3a1508);box-shadow:-10px 0 0 #d8d8d8 inset}
.hero-title{left:711px;top:203px;width:414px;height:130px;background:rgba(255,255,255,.9);padding:22px 45px}
.hero-title h1{font-size:42px;font-weight:900;color:var(--red);line-height:1.05}
.hero-dots{left:567px;top:488px;display:flex;gap:12px}
.hero-dots span{width:13px;height:13px;border-radius:50%;background:var(--red)}
.hero-dots span:first-child{background:#dcdcdc}

/* novels */
.novels{left:0;top:632px;width:1200px;height:512px;overflow:hidden}
.novels svg.band{position:absolute;left:0;top:0}
.novel-book{left:797px;top:39px;width:210px;height:394px;background:linear-gradient(165deg,#3a2210,#a0401a 50%,#2a1208);box-shadow:10px 0 0 #cfcfcf inset,20px 10px 25px rgba(0,0,0,.3)}
.section-head{font-size:32px;font-weight:700;color:var(--ink);letter-spacing:.5px;line-height:1}
.section-sub{font-size:24px;font-weight:700;color:var(--red);line-height:1}
.body-copy{font-size:13.5px;line-height:26px;color:var(--text)}
.btn{display:flex;align-items:center;justify-content:center;height:41px;color:var(--white);font-size:14px;font-weight:700;letter-spacing:.3px}
.btn-grey{background:var(--btn-grey)}
.btn-orange{background:var(--orange)}

/* card rows */
.card-band{left:0;width:1200px;background:var(--grey-bg)}
.card{width:239px;height:219px;background:linear-gradient(45deg,var(--red) 0%,#8e0f1c 45%,var(--red-deep) 100%);color:var(--white);text-align:center}
.card svg{position:absolute;left:94px;top:43px}
.card h3{position:absolute;left:0;right:0;top:118px;font-size:19px;font-weight:700;line-height:1}
.card p{position:absolute;left:12px;right:12px;top:149px;font-size:14px;line-height:23px}
.arrow{width:20px;height:28px}

/* author */
.author{left:0;top:1540px;width:1200px;height:471px;overflow:hidden}
.author-photo{left:137px;top:67px;width:266px;height:353px;background:linear-gradient(180deg,#a9c8e6 0%,#c9dcec 40%,#b9ad98 62%,#8f8271 100%)}

/* footer */
.footer-col h4{font-size:14px;font-weight:700;color:var(--ink);margin-bottom:13px}
.footer-col li{list-style:none;font-size:12.5px;color:var(--ink);height:30.5px}
.signup-input{left:799px;top:2439px;width:201px;height:38px;background:#e6e6e6;font-size:12px;color:#555;padding:12px 13px}
.signup-go{left:1000px;top:2439px;width:41px;height:38px;background:var(--red);color:var(--white);font-size:13px;font-weight:700;display:flex;align-items:center;justify-content:center}
.social{left:799px;top:2504px;display:flex;gap:14px;font-size:12.5px;font-weight:700;color:var(--ink)}
.copyright{left:799px;top:2538px;font-size:12.5px;line-height:22px;color:var(--ink)}
</style>
</head>
<body>

<header class="abs site-header">
  <div class="abs brand-art" role="img" aria-label="Dark fantasy artwork banner behind the author name"></div>
  <div class="abs brand-name">MARCUS FELLWRIGHT</div>
  <div class="abs brand-tagline">The Legend of Varethon</div>
  <nav class="abs main-nav">
    <a href="#">HOME</a><a href="#">NOVELS</a><a href="#">WORLD</a><a href="#">AUTHOR</a>
  </nav>
</header>

<section class="abs hero">
  <div class="abs hero-book" role="img" aria-label="Book cover of the first novel, a fiery demon illustration"></div>
  <div class="abs hero-title"><h1>THE LEGEND OF VARETHON</h1></div>
  <div class="abs hero-dots"><span></span><span></span><span></span></div>
</section>

<section class="abs novels">
  <svg class="band" width="1200" height="512" viewBox="0 0 1200 512"><polygon points="0,0 1200,0 1200,367" fill="#222222"/></svg>
  <div class="abs novel-book" role="img" aria-label="Book cover of the second novel, a figure among dark trees"></div>
  <h2 class="abs section-head" style="left:114px;top:172px">NOVELS</h2>
  <h3 class="abs section-sub" style="left:115px;top:227px">The Legend of Varethon</h3>
  <p class="abs body-copy" style="left:115px;top:268px;width:570px">The Age of Man, so quickly heralded, is already under siege.&nbsp; Shaken by the catastrophic war with the Demon Queen Morvessa, Calderia wrestles with a new world of possibility and potential disaster.</p>
  <div class="abs btn btn-grey" style="left:116px;top:382px;width:150px">MORE INFO</div>
  <div class="abs btn btn-orange" style="left:280px;top:382px;width:151px">BUY NOW</div>
</section>

<section class="abs card-band" style="top:1144px;height:396px">
  <h2 class="abs section-head" style="left:0;width:1200px;text-align:center;top:50px">WORLD</h2>
  <svg class="abs arrow" style="left:46px;top:206px" viewBox="0 0 20 28"><path d="M14 4 L5 14 L14 24" stroke="#222" stroke-width="4" fill="none"/></svg>
  <svg class="abs arrow" style="left:1136px;top:206px" viewBox="0 0 20 28"><path d="M6 4 L15 14 L6 24" stroke="#222" stroke-width="4" fill="none"/></svg>

  <div class="abs card" style="left:75px;top:110px">
    <svg width="52" height="50" viewBox="0 0 52 50"><path d="M26 2a11 11 0 0 1 11 11c0 8-11 20-11 20S15 21 15 13A11 11 0 0 1 26 2z" fill="#fff"/><circle cx="26" cy="13" r="4" fill="#8e0f1c"/><polygon points="10,30 18,30 26,40 34,30 42,30 50,48 2,48" fill="#fff"/></svg>
    <h3>MAPS</h3><p>View the lands of The Legend of Varethon.</p>
  </div>
  <div class="abs card" style="left:347px;top:110px">
    <svg width="52" height="50" viewBox="0 0 52 50"><circle cx="26" cy="12" r="8" fill="#fff"/><circle cx="11" cy="17" r="6" fill="#fff"/><circle cx="41" cy="17" r="6" fill="#fff"/><path d="M12 46v-8a14 14 0 0 1 28 0v8z" fill="#fff"/><path d="M0 44v-6a11 11 0 0 1 14-10v18z M52 44v-6a11 11 0 0 0-14-10v18z" fill="#fff"/></svg>
    <h3>CHARACTERS</h3><p>View the characters and peoples of The Legend of&nbsp; Varethon.</p>
  </div>
  <div class="abs card" style="left:617px;top:110px">
    <svg width="52" height="50" viewBox="0 0 52 50"><path d="M26 1a15 15 0 0 1 15 15c0 12-15 33-15 33S11 28 11 16A15 15 0 0 1 26 1z" fill="#fff"/><circle cx="26" cy="16" r="6" fill="#8e0f1c"/></svg>
    <h3>LOCATIONS</h3><p>View the geographic locations of The Legend of Varethon.</p>
  </div>
  <div class="abs card" style="left:888px;top:110px">
    <svg width="52" height="50" viewBox="0 0 52 50"><path d="M46 3 L50 7 L26 31 L20 25 Z" fill="#fff"/><path d="M18 27 L24 33 C22 42 12 46 4 44 C10 40 8 30 18 27Z" fill="#fff"/></svg>
    <h3>ARTIFACTS</h3><p>View the artifacts and powers of The Legend of Varethon.</p>
  </div>
</section>

<section class="abs author">
  <svg class="abs" style="left:0;top:0" width="1200" height="471" viewBox="0 0 1200 471"><polygon points="0,0 1200,0 0,366" fill="#222222"/></svg>
  <div class="abs author-photo" role="img" aria-label="Photo of the author seated on a beach"></div>
  <h2 class="abs section-head" style="right:74px;top:175px">AUTHOR</h2>
  <h3 class="abs section-sub" style="right:74px;top:231px">Biography</h3>
  <p class="abs body-copy" style="right:74px;top:271px;width:650px;text-align:right">Weaned on the likes of The Warden of the Vales and Star Voyages, Marcus took to writing fantasy adventure, it seems, almost as soon as he learned to read. By the time he hit grade school, he was writing 30-page stories in lieu of the two or three pages expected of all students on a monthly basis</p>
  <div class="abs btn btn-grey" style="left:976px;top:382px;width:150px">MORE INFO</div>
</section>

<section class="abs card-band" style="top:2011px;height:351px">
  <svg class="abs arrow" style="left:46px;top:160px" viewBox="0 0 20 28"><path d="M14 4 L5 14 L14 24" stroke="#222" stroke-width="4" fill="none"/></svg>
  <svg class="abs arrow" style="left:1136px;top:160px" viewBox="0 0 20 28"><path d="M6 4 L15 14 L6 24" stroke="#222" stroke-width="4" fill="none"/></svg>

  <div class="abs card" style="left:75px;top:65px">
    <svg width="52" height="50" viewBox="0 0 52 50"><path d="M12 2h20l10 10v36H12z" fill="#fff"/><rect x="18" y="20" width="18" height="3" fill="#8e0f1c"/><rect x="18" y="28" width="18" height="3" fill="#8e0f1c"/><rect x="18" y="36" width="18" height="3" fill="#8e0f1c"/></svg>
    <h3>NEWS</h3><p>View the lands of The Legend of Varethon.</p>
  </div>
  <div class="abs card" style="left:347px;top:65px">
    <svg width="52" height="50" viewBox="0 0 52 50"><rect x="5" y="7" width="42" height="40" rx="3" fill="#fff"/><rect x="9" y="17" width="34" height="26" fill="#8e0f1c"/><g fill="#fff"><rect x="11" y="19" width="6" height="5"/><rect x="20" y="19" width="6" height="5"/><rect x="29" y="19" width="6" height="5"/><rect x="11" y="27" width="6" height="5"/><rect x="20" y="27" width="6" height="5"/><rect x="29" y="27" width="6" height="5"/><rect x="11" y="35" width="6" height="5"/><rect x="20" y="35" width="6" height="5"/></g><rect x="13" y="2" width="4" height="9" fill="#fff"/><rect x="35" y="2" width="4" height="9" fill="#fff"/></svg>
    <h3>EVENTS</h3><p>View the characters and peoples of The Legend of&nbsp; Varethon.</p>
  </div>
  <div class="abs card" style="left:617px;top:65px">
    <svg width="52" height="50" viewBox="0 0 52 50"><rect x="19" y="1" width="14" height="28" rx="7" fill="#fff"/><path d="M12 20a14 14 0 0 0 28 0" stroke="#fff" stroke-width="3" fill="none"/><rect x="24" y="34" width="4" height="10" fill="#fff"/><rect x="16" y="44" width="20" height="4" fill="#fff"/></svg>
    <h3>INTERVIEWS</h3><p>View the geographic locations of The Legend of Varethon.</p>
  </div>
  <div class="abs card" style="left:888px;top:65px">
    <svg width="52" height="50" viewBox="0 0 52 50"><ellipse cx="21" cy="18" rx="19" ry="14" fill="#fff"/><path d="M8 28 L4 38 L16 30Z" fill="#fff"/><ellipse cx="35" cy="30" rx="15" ry="11" fill="#fff" stroke="#8e0f1c" stroke-width="2"/><path d="M42 39 L48 46 L38 40Z" fill="#fff"/></svg>
    <h3>Q&amp;A</h3><p>View the artifacts and powers of The Legend of Varethon.</p>
  </div>
</section>

<footer>
  <div class="abs footer-col" style="left:79px;top:2406px"><h4>NOVELS</h4><ul><li>Summaries</li><li>Excerpts</li><li>Reviews</li><li>Buy Online</li><li>Signed Copies</li></ul></div>
  <div class="abs footer-col" style="left:328px;top:2406px"><h4>WORLD</h4><ul><li>Maps</li><li>Characters</li><li>Locations</li><li>Artifacts</li><li>Gallery</li></ul></div>
  <div class="abs footer-col" style="left:575px;top:2406px"><h4>AUTHOR</h4><ul><li>Bio</li><li>News</li><li>Events</li><li>Interviews</li><li>Q&amp;A</li></ul></div>
  <div class="abs footer-col" style="left:808px;top:2406px"><h4>EMAIL SIGN UP</h4></div>
  <div class="abs signup-input">Enter Email Address</div>
  <div class="abs signup-go">GO</div>
  <div class="abs social"><span>Facely</span><span>Pictora</span><span>Chirpr</span><span>Linkwell</span><span>Vidtube</span></div>
  <p class="abs copyright">Copyright © 2018, Company Name<br>All Right reserved.</p>
</footer>

</body>
</html>
```